KDWB Business Card

Looking for a business card design to incorporate our branding. We want to only use the colors listing in the Branding Package (attached).
Updates

Target Market(s)

People who need their phone or device fixed.

Industry/Entity Type

Electronics

Contact Information for Business Card

Please use:

Brightwick Gadget Clinic LLC
4810 E Harlow Ridge Rd
Suite 417
San Antonio, TX 78163

Marcus Delgrove, Store Manager

(210) 555-0147

Requirements
Must have
• Must include the colors that are contained within the Branding Package PDF file.

```html
<!DOCTYPE html>
<html lang="en">
<head>
<meta charset="utf-8">
<title>Brightwick Gadget Clinic – Business Card</title>
<link href="https://fonts.googleapis.com/css2?family=Quicksand:wght@500;600&family=Roboto:wght@400;500&display=swap" rel="stylesheet">
<style>
  :root {
    --orange: #f0511f;
    --orange-soft: #f37b3c;
    --ink: #3a3a3a;
    --grey: #6b6b6b;
    --paper: #ffffff;
    --backdrop: #e7e6e4;
    --photo-blue: #2f63b8;
    --photo-light: #e9eef2;
  }
  * { box-sizing: border-box; margin: 0; padding: 0; }
  html, body { width: 1200px; height: 873px; overflow: hidden; }
  body {
    background: var(--backdrop);
    font-family: "Roboto", Arial, sans-serif;
    color: var(--ink);
    position: relative;
  }
  .card {
    position: absolute;
    background: var(--paper);
    box-shadow: 0 6px 18px rgba(0,0,0,0.18);
    overflow: hidden;
  }
  /* Front: portrait */
  .card-front { left: 130px; top: 148px; width: 330px; height: 578px; }
  .front-photo {
    position: absolute; left: 0; top: 0; width: 100%; height: 250px;
    background: linear-gradient(120deg, var(--photo-blue) 0%, #3f79c8 45%, var(--photo-light) 80%);
  }
  .front-curve { position: absolute; left: 0; top: 150px; width: 100%; height: 130px; }
  .brand {
    display: flex; align-items: center; gap: 10px;
    font-family: "Quicksand", sans-serif; font-weight: 600;
    color: var(--orange);
  }
  .brand-mark { background: var(--orange); border-radius: 8px; flex: none; }
  .front-brand { position: absolute; left: 40px; top: 300px; font-size: 21px; }
  .front-brand .brand-mark { width: 30px; height: 30px; }
  .person { position: absolute; right: 28px; top: 372px; text-align: right; }
  .person-name { font-size: 22px; font-weight: 400; color: var(--ink); }
  .person-title { font-size: 12px; color: var(--orange); margin-top: 2px; }
  .contact-list {
    position: absolute; right: 28px; top: 436px; list-style: none;
    text-align: right; font-size: 12.5px; color: var(--ink);
  }
  .contact-list li { display: flex; justify-content: flex-end; align-items: flex-start; gap: 8px; margin-bottom: 9px; line-height: 1.35; }
  .contact-icon { width: 14px; height: 14px; flex: none; margin-top: 1px; }
  /* Back: landscape */
  .card-back { left: 560px; top: 258px; width: 540px; height: 310px; }
  .back-brand {
    position: absolute; left: 0; right: 0; top: 50%; transform: translateY(-50%);
    justify-content: center; font-size: 30px;
  }
  .back-brand .brand-mark { width: 42px; height: 42px; border-radius: 10px; }
</style>
</head>
<body>
  <section class="card card-front" aria-label="Business card front">
    <div class="front-photo" role="img" aria-label="Photo of hands repairing an opened smartphone"></div>
    <svg class="front-curve" viewBox="0 0 330 130" preserveAspectRatio="none" aria-hidden="true">
      <path d="M0 130 L0 100 C110 92 250 60 330 0 L330 130 Z" fill="var(--orange)"/>
      <path d="M0 130 L0 110 C120 104 255 72 330 16 L330 130 Z" fill="var(--paper)"/>
    </svg>

    <div class="brand front-brand">
      <span class="brand-mark"></span>
      <span class="brand-name">Brightwick Gadget Clinic</span>
    </div>

    <div class="person">
      <p class="person-name">Marcus Delgrove</p>
      <p class="person-title">Store Manager</p>
    </div>

    <ul class="contact-list">
      <li><span>(210) 555-0147</span>
        <svg class="contact-icon" viewBox="0 0 14 14"><rect width="14" height="14" fill="var(--orange)"/><path d="M4 3l2 0 1 2.5-1.2 1a5 5 0 0 0 2 2l1-1.2 2.5 1v2c-4 .5-7.8-3.3-7.3-7.3z" fill="#fff"/></svg></li>
      <li><span>marcus@brightwickclinic.com</span>
        <svg class="contact-icon" viewBox="0 0 14 14"><rect width="14" height="14" fill="var(--orange)"/><rect x="3" y="4" width="8" height="6" fill="none" stroke="#fff"/><path d="M3 4l4 3.5L11 4" fill="none" stroke="#fff"/></svg></li>
      <li><span>www.brightwickclinic.com</span>
        <svg class="contact-icon" viewBox="0 0 14 14"><rect width="14" height="14" fill="var(--orange)"/><circle cx="7" cy="7" r="4" fill="none" stroke="#fff"/><path d="M3 7h8M7 3v8" stroke="#fff"/></svg></li>
      <li><span>4810 E Harlow Ridge Rd<br>Suite 417, San Antonio, TX 78163</span>
        <svg class="contact-icon" viewBox="0 0 14 14"><rect width="14" height="14" fill="var(--orange)"/><path d="M7 12s-3.5-4-3.5-6.2a3.5 3.5 0 0 1 7 0C10.5 8 7 12 7 12z" fill="#fff"/><circle cx="7" cy="5.8" r="1.2" fill="var(--orange)"/></svg></li>
    </ul>
  </section>

  <section class="card card-back" aria-label="Business card back">
    <div class="brand back-brand">
      <span class="brand-mark"></span>
      <span class="brand-name">Brightwick Gadget Clinic</span>
    </div>
  </section>
</body>
</html>
```